Alaska Law Firm Needs a Sticker Design

We need a design for stickers to put on already-printed brochures. We mail the brochures to potential clients so they can learn more about accident-induced injuries, insurance claims, legal representation, and our own law firm.

One of our lawyers wrote a book that provides a helpful overview of personal injury claims. We are offering this book for free to anyone who calls and requests it. Therefore, the sticker design should include one of the following phrases, or something very similar:
a) "Still have questions? Call and request our book-- for free!"
b) "Still have questions about auto accident claims? Call and request our book today."
c) "Still have questions about filing a claim? Call and request a free copy of our book."
d) "Still have questions? Call us today to request a free copy of our book, Clear Lanes Ahead."
e) "To learn more about automobile accidents and insurance, call today and request a free copy of our book."

The sticker should be approximately 3"x3" and may be a circle, square, rectangle, or ellipsis. The sticker will be placed on the back of the folder, which is light blue. We would like the sticker to match the color scheme of our website and the folder.

I will upload an image of the book cover as soon as I obtain it.

Law Firm

Font styles to use
Serif
Sans Serif

Requirements
Should not have
• Bright colors that aren't already used in the folder design. e.g. no bright orange, pink, chartreuse, turquoise, yellow, red.

```html
<!DOCTYPE html>
<html lang="en">
<head>
<meta charset="utf-8">
<title>Still Have Questions – Sticker</title>
<link href="https://fonts.googleapis.com/css2?family=Bebas+Neue&family=Oswald:wght@400&family=Open+Sans:wght@400;800&display=swap" rel="stylesheet">
<style>
  :root {
    --navy: #143f6b;
    --sky: #d7e5f6;
    --paper: #ffffff;
    --backdrop: #ebebeb;
    --leaf: #6f9a4a;
    --meadow: #a9c98a;
    --haze: #d9e4ec;
  }
  html, body {
    margin: 0;
    padding: 0;
    width: 1200px;
    height: 1085px;
    overflow: hidden;
    background: var(--backdrop);
  }
  .sticker {
    position: absolute;
    left: 120px;
    top: 62px;
    width: 960px;
    height: 960px;
    background: var(--paper);
    box-sizing: border-box;
    padding: 18px;
  }
  .sticker-face {
    position: relative;
    width: 100%;
    height: 100%;
    background: var(--sky);
    overflow: hidden;
  }
  .headline-main {
    position: absolute;
    top: 74px;
    left: 0;
    width: 100%;
    margin: 0;
    text-align: center;
    font-family: "Bebas Neue", sans-serif;
    font-weight: 400;
    font-size: 164px;
    line-height: 1;
    color: var(--navy);
    letter-spacing: 2px;
  }
  .headline-sub {
    position: absolute;
    top: 226px;
    left: 0;
    width: 100%;
    margin: 0;
    text-align: center;
    font-family: "Bebas Neue", sans-serif;
    font-weight: 400;
    font-size: 78px;
    line-height: 1;
    letter-spacing: 20px;
    padding-left: 20px;
    box-sizing: border-box;
    color: var(--paper);
    -webkit-text-stroke: 3px var(--navy);
  }
  .offer-band {
    position: absolute;
    left: 0;
    top: 426px;
    width: 100%;
    height: 303px;
    background: var(--navy);
  }
  .offer-call {
    position: absolute;
    left: 88px;
    top: 444px;
    margin: 0;
    font-family: "Bebas Neue", sans-serif;
    font-size: 48px;
    line-height: 1;
    color: var(--paper);
    letter-spacing: 0.5px;
  }
  .offer-phone {
    position: absolute;
    left: 52px;
    top: 512px;
    margin: 0;
    font-family: "Oswald", sans-serif;
    font-weight: 400;
    font-size: 66px;
    line-height: 1;
    color: var(--paper);
    letter-spacing: 2px;
  }
  .offer-free {
    position: absolute;
    left: 66px;
    top: 602px;
    margin: 0;
    font-family: "Bebas Neue", sans-serif;
    font-size: 134px;
    line-height: 1;
    color: var(--paper);
    letter-spacing: 2px;
  }
  .book-cover {
    position: absolute;
    left: 552px;
    top: 340px;
    width: 296px;
    height: 484px;
    background: var(--paper);
    box-shadow: 6px 8px 14px rgba(0,0,0,0.25);
    display: flex;
    flex-direction: column;
  }
  .book-author {
    margin: 22px 0 4px;
    text-align: center;
    font-family: "Open Sans", sans-serif;
    font-weight: 400;
    font-size: 17px;
    color: var(--navy);
  }
  .book-title {
    margin: 0 10px 8px;
    text-align: center;
    font-family: "Open Sans", sans-serif;
    font-weight: 800;
    font-size: 31px;
    line-height: 1;
    color: var(--navy);
    text-transform: uppercase;
  }
  .book-photo {
    flex: 1;
    background: linear-gradient(180deg, var(--haze) 0%, var(--meadow) 55%, var(--leaf) 100%);
  }
  .book-tagline {
    margin: 0;
    padding: 8px 12px 10px;
    background: var(--navy);
    text-align: center;
    font-family: "Open Sans", sans-serif;
    font-weight: 400;
    font-size: 14px;
    line-height: 1.2;
    color: var(--paper);
    text-transform: uppercase;
  }
</style>
</head>
<body>
  <div class="sticker">
    <div class="sticker-face">
      <h1 class="headline-main">Still Have</h1>
      <p class="headline-sub">Questions?</p>

      <div class="offer-band"></div>
      <p class="offer-call">Call &amp; Request Our Book</p>
      <p class="offer-phone">(907 555-0148)</p>
      <p class="offer-free">For Free !!</p>

      <div class="book-cover">
        <p class="book-author">DANIEL R. WHITFIELD</p>
        <p class="book-title">Clear Lanes Ahead</p>
        <div class="book-photo" role="img" aria-label="Photo of a smiling family lying on the grass in a park with a red car"></div>
        <p class="book-tagline">The right way to handle<br>your auto accident claim</p>
      </div>
    </div>
  </div>
</body>
</html>
```